Business Card For Halvenmoor Financial Consulting

Hi, I would like a business card designed. Bold, modern.
Please use the same design as the logo. I have also attached the website design to see the overall theme.
Wordmark Font
Color: Hex: #01AEF7

```html
<!DOCTYPE html>
<html lang="en">
<head>
<meta charset="utf-8">
<title>Halvenmoor Consulting – Business Card</title>
<link rel="stylesheet" href="https://fonts.googleapis.com/css2?family=Montserrat:wght@600;700&family=Inter:wght@400;500&display=swap">
<style>
  :root {
    --backdrop: #3a3a3a;
    --card: #18212b;
    --card-deep: #121a22;
    --accent: #01aef7;
    --accent-soft: #2a9fd6;
    --ink: #f2f5f7;
    --ink-muted: #c9d2da;
  }
  * { box-sizing: border-box; margin: 0; padding: 0; }
  html, body { width: 1200px; height: 801px; overflow: hidden; }
  body {
    background: var(--backdrop);
    font-family: "Inter", Arial, sans-serif;
    position: relative;
  }
  .card {
    position: absolute;
    top: 252px;
    width: 520px;
    height: 297px;
    background: var(--card);
    border-bottom: 3px solid var(--accent);
    overflow: hidden;
  }
  .card--front { left: 60px; }
  .card--back { left: 620px; }

  /* Front */
  .brand {
    position: absolute;
    top: 46px;
    left: 178px;
    display: flex;
    align-items: center;
    gap: 10px;
  }
  .brand__mark {
    width: 30px; height: 30px;
    border: 3px solid var(--accent);
  }
  .brand__name {
    font-family: "Montserrat", Arial, sans-serif;
    font-weight: 700;
    font-size: 26px;
    letter-spacing: 1px;
    color: var(--ink);
    line-height: 1;
  }
  .brand__tagline {
    font-family: "Montserrat", Arial, sans-serif;
    font-weight: 700;
    font-size: 26px;
    color: var(--accent);
    line-height: 1;
  }
  .divider {
    position: absolute;
    left: 30px; right: 30px;
    top: 118px;
    height: 1px;
    background: var(--accent);
  }
  .person {
    position: absolute;
    left: 30px;
    top: 146px;
  }
  .person__name {
    font-family: "Montserrat", Arial, sans-serif;
    font-weight: 700;
    font-size: 20px;
    color: var(--accent);
    letter-spacing: 0.5px;
    text-transform: uppercase;
  }
  .person__title {
    font-size: 13px;
    color: var(--ink);
    margin-top: 2px;
  }
  .person__rule {
    width: 200px;
    height: 1px;
    background: var(--accent-soft);
    margin: 12px 0 10px;
  }
  .contact { list-style: none; }
  .contact li {
    display: flex;
    align-items: center;
    gap: 8px;
    font-size: 12.5px;
    color: var(--ink);
    line-height: 1.55;
  }
  .contact svg { width: 11px; height: 11px; fill: var(--accent); flex: none; }
  .address {
    position: absolute;
    right: 30px;
    top: 146px;
    text-align: right;
    font-size: 12.5px;
    line-height: 1.55;
    color: var(--ink);
  }

  /* Back */
  .back-pattern {
    position: absolute;
    inset: 0;
    background: radial-gradient(ellipse at 20% 70%, #2b3a4a 0%, var(--card) 55%, var(--card-deep) 100%);
  }
  .back-brand {
    position: absolute;
    right: 40px;
    top: 132px;
    font-family: "Montserrat", Arial, sans-serif;
    font-weight: 700;
    font-size: 18px;
    color: var(--accent);
    letter-spacing: 1px;
    padding: 6px 10px;
    background: var(--card);
  }
</style>
</head>
<body>
  <section class="card card--front" aria-label="Business card front">
    <div class="brand">
      <span class="brand__mark"></span>
      <div>
        <div class="brand__name">HALVENMOOR <span class="brand__tagline">CONSULTING</span></div>
      </div>
    </div>
    <div class="divider"></div>
    <div class="person">
      <div class="person__name">Marek Tolliver</div>
      <div class="person__title">President</div>
      <div class="person__rule"></div>
      <ul class="contact">
        <li><svg viewBox="0 0 24 24"><path d="M6.6 10.8a15 15 0 0 0 6.6 6.6l2.2-2.2a1 1 0 0 1 1-.25 11.4 11.4 0 0 0 3.6.57 1 1 0 0 1 1 1V20a1 1 0 0 1-1 1A17 17 0 0 1 3 4a1 1 0 0 1 1-1h3.5a1 1 0 0 1 1 1c0 1.25.2 2.45.57 3.57a1 1 0 0 1-.25 1z"/></svg>555-013-4720</li>
        <li><svg viewBox="0 0 24 24"><path d="M2 5h20v14H2zm2 2v.5l8 5 8-5V7l-8 5z"/></svg>info@HalvenmoorConsulting.com</li>
        <li><svg viewBox="0 0 24 24"><circle cx="12" cy="12" r="10"/></svg>www.HalvenmoorConsulting.com</li>
      </ul>
    </div>
    <div class="address">
      18 Corwell Marina Dr<br>
      Brightwater CA 90412
    </div>
  </section>

  <section class="card card--back" aria-label="Business card back">
    <div class="back-pattern" role="img" aria-label="Tonal repeating brand pattern across the card back"></div>
    <div class="back-brand">HALVENMOOR</div>
  </section>
</body>
</html>
```